Corvel Capital LLC

Need Professional Business cards for New Investment Fund

Target Market(s)

High Quality investors

Industry/Entity Type

Financial

Contact Information for Business Card

Phone Number +1 555 284 6190
Name Lukas Varenko
Title Fund Manager
email lv@FundCorvel.com
Website www.FundCorvel.com

Colors

Designer to choose colors to be used in the design.

Requirements
Must have
• Must have our Logo and all of the above. Must be made so lettering and loge can be raised

```html
<!DOCTYPE html>
<html lang="en">
<head>
<meta charset="utf-8">
<title>Business Card – Fund Manager</title>
<link href="https://fonts.googleapis.com/css2?family=Open+Sans:wght@400;600;700&display=swap" rel="stylesheet">
<style>
  :root {
    --backdrop: #2c2d30;
    --lime: #1de80a;
    --charcoal: #3d4a3f;
    --ink: #111611;
    --paper: #ffffff;
    --paper-shade: #e9eaea;
    --back-green: #3a4538;
  }
  * { margin: 0; padding: 0; box-sizing: border-box; }
  html, body {
    width: 1200px; height: 1000px; overflow: hidden;
    background: var(--backdrop);
    font-family: "Open Sans", Arial, sans-serif;
  }
  .card {
    position: absolute;
    left: 215px;
    width: 770px; height: 440px;
    overflow: hidden;
    box-shadow: 0 10px 30px rgba(0,0,0,.45);
  }
  .card--front {
    top: 40px;
    background: linear-gradient(160deg, var(--paper) 55%, var(--paper-shade) 100%);
  }
  .card--back { top: 520px; background: var(--back-green); }

  .front-bands { position: absolute; inset: 0; }

  .contact-block {
    position: absolute; left: 58px; top: 118px;
    color: var(--ink);
  }
  .contact-name {
    font-weight: 700; font-size: 23px; letter-spacing: .5px;
    text-transform: uppercase;
  }
  .contact-title { font-weight: 700; font-size: 15px; margin: 2px 0 16px 2px; }
  .contact-list { list-style: none; font-size: 16px; line-height: 23px; }
  .contact-list li { display: flex; align-items: center; gap: 9px; }
  .contact-list svg { width: 14px; height: 14px; fill: var(--ink); flex: none; }

  .brand-name {
    position: absolute; left: 470px; top: 196px;
    width: 280px; text-align: center;
    font-weight: 600; font-size: 38px; letter-spacing: 3px;
    color: var(--charcoal);
  }

  .back-pattern {
    position: absolute; inset: 0;
    background: linear-gradient(135deg, #414d3f, #343e33);
  }
  .back-brand {
    position: absolute; right: 40px; bottom: 34px;
    font-weight: 600; font-size: 20px; letter-spacing: 2px;
    color: var(--paper);
  }
</style>
</head>
<body>

<section class="card card--front">
  <svg class="front-bands" viewBox="0 0 770 440" aria-hidden="true">
    <polygon points="0,0 440,0 335,440 0,440" fill="var(--lime)"/>
    <polygon points="440,0 464,0 359,440 335,440" fill="var(--charcoal)"/>
    <polygon points="472,0 490,0 385,440 367,440" fill="var(--lime)"/>
  </svg>

  <div class="contact-block">
    <h1 class="contact-name">Lukas Varenko</h1>
    <p class="contact-title">Fund Manager</p>
    <ul class="contact-list">
      <li>
        <svg viewBox="0 0 16 16"><path d="M3 1h3l1.5 4-2 1.3a9 9 0 0 0 4.2 4.2L11 8.5l4 1.5v3a2 2 0 0 1-2 2A12 12 0 0 1 1 3a2 2 0 0 1 2-2z"/></svg>
        +1 555 284 6190
      </li>
      <li>
        <svg viewBox="0 0 16 16"><path d="M1 3h14v10H1zM1 3l7 6 7-6" stroke="#fff" stroke-width="1"/></svg>
        lv@FundCorvel.com
      </li>
      <li>
        <svg viewBox="0 0 16 16"><circle cx="8" cy="8" r="7"/><path d="M1 8h14M8 1c3 3 3 11 0 14M8 1c-3 3-3 11 0 14" stroke="var(--lime)" stroke-width="1" fill="none"/></svg>
        www.FundCorvel.com
      </li>
    </ul>
  </div>

  <p class="brand-name">HALVORNE</p>
</section>

<section class="card card--back">
  <div class="back-pattern" role="img" aria-label="Tonal embossed repeat pattern across the card back"></div>
  <p class="back-brand">HALVORNE</p>
</section>

</body>
</html>
```